Its time for a new website

We are at a point now where we are in desperate need of a new website. It was last updated 2006 but still looks like its 1995. We are looking for something eye catching to our clients but easy to navigate and add/remove photos of jobs/trucks and information. Our key business is the manufacture of fire appliances and resale of parts and equipment.

www.kestrelrigs.com.au

Coding

Coded - Design and coding required

Number of Pages Required

5+ page

Requirements
Must have
• Logo

```html
<!DOCTYPE html>
<html lang="en">
<head>
<meta charset="utf-8">
<title>Kestrel Rigs</title>
<link href="https://fonts.googleapis.com/css2?family=Open+Sans:wght@400;600;700;800&display=swap" rel="stylesheet">
<style>
:root{
  --header-bg:#1e1513;
  --footer-bg:#1c1412;
  --body-bg:#232323;
  --red:#9b1410;
  --red-light:#b3201b;
  --blue:#1783c9;
  --white:#ffffff;
  --muted:#b9b9b9;
  --line:#3a2c2a;
}
*{margin:0;padding:0;box-sizing:border-box}
html,body{width:872px;height:1200px;overflow:hidden;background:var(--body-bg)}
body{position:relative;font-family:'Open Sans',sans-serif;color:var(--white)}
.abs{position:absolute}
.site-header{left:0;top:0;width:872px;height:100px;background:var(--header-bg)}
.brand{left:72px;top:30px;display:flex;align-items:center;gap:10px}
.brand-dot{width:34px;height:34px;border-radius:50%;background:var(--red-light)}
.brand-name{font-size:20px;font-weight:700;color:var(--blue)}
.help{right:72px;top:40px;display:flex;align-items:center;gap:8px;font-size:15px}
.help-label{color:var(--blue)}
.help-phone{color:var(--white);font-size:16px}
.main-nav{left:0;top:100px;width:872px;height:48px;background:linear-gradient(#b3201b,#8a1410)}
.nav-item{top:0;height:48px;display:flex;align-items:center;justify-content:center;font-size:8.5px;color:var(--white);border-right:1px solid rgba(0,0,0,.25)}
.nav-item.active{background:var(--blue)}
.nav-caret{position:absolute;bottom:9px;left:50%;margin-left:-3px}
.hero{left:0;top:148px;width:872px;height:428px;background:linear-gradient(100deg,#4b5766 0%,#56626e 35%,#7a3a3c 55%,#9a2a2a 70%,#5d6670 100%)}
.hero-title{left:73px;top:258px;font-size:29px;font-weight:800;letter-spacing:.5px}
.hero-sub{left:74px;top:300px;font-size:16px;font-weight:700;color:var(--blue)}
.hero-text{left:75px;top:332px;width:400px;font-size:9.5px;line-height:15px}
.btn{display:flex;align-items:center;justify-content:center;color:var(--white)}
.btn-red{background:var(--red-light)}
.btn-blue{background:var(--blue)}
.hero-btn{left:74px;top:388px;width:112px;height:31px;font-size:12px}
.hero-arrow{top:296px;width:30px;height:30px}
.news{left:72px;top:545px;width:178px;height:471px;background:var(--red)}
.news-title{left:87px;top:562px;font-size:13px;font-weight:700}
.news-date{left:86px;width:148px;height:29px;background:var(--blue);font-size:10px;padding-left:8px;display:flex;align-items:center}
.news-photo{left:86px;width:148px;height:83px}
.news-text{left:88px;width:150px;font-size:9px;line-height:15px}
.news-text b{color:#f5b400;font-weight:700;margin-left:6px}
.news-rule{left:88px;width:144px;height:1px;background:rgba(255,255,255,.15)}
.news-all{left:93px;top:974px;font-size:11.5px}
.news-all b{color:#f5b400}
.col-head{top:590px;width:223px;height:28px;font-size:11.5px;padding-left:20px;display:flex;align-items:center}
.col-photo{top:646px;width:223px;height:204px;border:1px solid #9a9a9a}
.col-sub{top:866px;font-size:8.5px;font-weight:400}
.col-text{top:890px;width:210px;font-size:9px;line-height:15px;color:var(--muted)}
.col-btn{top:973px;width:98px;height:27px;font-size:8.5px}
.site-footer{left:0;top:1056px;width:872px;height:144px;background:var(--footer-bg)}
.foot-title{top:1080px;font-size:15px}
.foot-lines{left:73px;top:1116px;font-size:8.5px;line-height:15.5px;color:#cfcfcf}
.foot-lines span{display:inline-block;width:36px}
.foot-rule{top:1076px;width:1px;height:100px;background:var(--line)}
.social{top:1121px;width:32px;height:32px;border-radius:50%}
.copyright{right:72px;top:1094px;font-size:10.5px}
.copyright em{font-style:normal;color:#c01c18}
.code{left:830px;top:1157px;font-size:10px;color:#cfcfcf}
</style>
</head>
<body>
<header class="site-header abs">
  <div class="brand abs"><span class="brand-dot"></span><span class="brand-name">Kestrel Rigs</span></div>
  <div class="help abs">
    <span class="help-label">Need Help?</span>
    <svg width="20" height="20" viewBox="0 0 24 24"><path fill="#c9201a" d="M6.6 10.8a15 15 0 0 0 6.6 6.6l2.2-2.2a1 1 0 0 1 1-.25 11.4 11.4 0 0 0 3.6.57 1 1 0 0 1 1 1V20a1 1 0 0 1-1 1A17 17 0 0 1 3 4a1 1 0 0 1 1-1h3.5a1 1 0 0 1 1 1c0 1.250.2 2.45.57 3.57a1 1 0 0 1-.25 1z"/></svg>
    <span class="help-phone">08 97730158</span>
  </div>
</header>

<nav class="main-nav abs">
  <div class="nav-item abs active" style="left:72px;width:97px">HOME</div>
  <div class="nav-item abs" style="left:169px;width:117px">ABOUT US</div>
  <div class="nav-item abs" style="left:286px;width:115px">SERVICES
    <svg class="nav-caret" width="6" height="4" viewBox="0 0 6 4"><path d="M0 0l3 3 3-3" stroke="#fff" fill="none"/></svg></div>
  <div class="nav-item abs" style="left:401px;width:137px">SLIP-ON UNITS</div>
  <div class="nav-item abs" style="left:538px;width:136px">CONTACT US</div>
  <div class="nav-item abs" style="left:674px;width:126px">NEW FOR 2006</div>
</nav>

<section class="hero abs" role="img" aria-label="Red fire truck tanker parked on a road"></section>
<h1 class="hero-title abs">KESTREL RIGS</h1>
<p class="hero-sub abs">Wandering Creek Western Australia</p>
<p class="hero-text abs">Kestrel Rigs manufacture quality fire truck and tender units in the South West region of Australia</p>
<a class="btn btn-red hero-btn abs">READ MORE</a>
<svg class="hero-arrow abs" style="left:19px" viewBox="0 0 30 30"><circle cx="15" cy="15" r="15" fill="#cfcfcf"/><path d="M17.5 8l-7 7 7 7" stroke="#444" stroke-width="3.5" fill="none"/></svg>
<svg class="hero-arrow abs" style="left:823px" viewBox="0 0 30 30"><circle cx="15" cy="15" r="15" fill="#cfcfcf"/><path d="M12.5 8l7 7-7 7" stroke="#444" stroke-width="3.5" fill="none"/></svg>

<aside class="news abs"></aside>
<h2 class="news-title abs">LATEST NEWS</h2>
<div class="news-date abs" style="top:590px">22 MARCH, 2015</div>
<div class="news-photo abs" style="top:619px;background:linear-gradient(90deg,#7a2a1a,#c04a1a 60%,#f0a030)" role="img" aria-label="Fire extinguisher spraying a stove fire"></div>
<p class="news-text abs" style="top:714px">At vero eos et accusamus et iusto odio dignissimos ducimus.<b>»</b></p>
<div class="news-rule abs" style="top:765px"></div>
<div class="news-date abs" style="top:786px">22 MARCH, 2015</div>
<div class="news-photo abs" style="top:815px;background:linear-gradient(90deg,#9aa7a0,#dfe6e0 60%,#c8d0c8)" role="img" aria-label="Hand pressing a wall alarm panel"></div>
<p class="news-text abs" style="top:910px">At vero eos et accusamus et iusto odio dignissimos ducimus.<b>»</b></p>
<div class="news-rule abs" style="top:963px"></div>
<a class="news-all abs">All News <b>»</b></a>

<div class="col-head btn-red abs" style="left:306px;justify-content:flex-start">WELCOME TO OUR WEBSITE</div>
<div class="col-photo abs" style="left:306px;background:linear-gradient(160deg,#6f6a55,#d88a2a 45%,#b24a1e 70%,#5c6a3a)" role="img" aria-label="Firefighters spraying water at a blaze"></div>
<p class="col-sub abs" style="left:310px">WANDERING CREEK WESTERN AUSTRALIA</p>
<p class="col-text abs" style="left:310px">Et harum quidem rerum facilis est et expedita distinctio. Nam libero tempore, cum soluta nobis est eligendi optio cumque nihil impedit quo minus id quod maxime.</p>
<a class="btn btn-red col-btn abs" style="left:310px">READ MORE</a>

<div class="col-head btn-blue abs" style="left:576px;justify-content:flex-start">OUR MANUFACTURE SERVICES</div>
<div class="col-photo abs" style="left:576px;background:linear-gradient(180deg,#8a8f94,#b3201b 35%,#c42a22 75%,#8a8a8a)" role="img" aria-label="Front view of a red fire engine"></div>
<p class="col-sub abs" style="left:580px">FOR ALL YOUR FIRE FIGHTING NEEDS</p>
<p class="col-text abs" style="left:580px">Et harum quidem rerum facilis est et expedita distinctio. Nam libero tempore, cum soluta nobis est eligendi optio cumque nihil impedit quo minus id quod maxime.</p>
<a class="btn btn-blue col-btn abs" style="left:581px">READ MORE</a>

<footer class="site-footer abs"></footer>
<h3 class="foot-title abs" style="left:72px;font-weight:400">CONTACT US</h3>
<p class="foot-lines abs"><span>Address</span>: Lot 14 Brennan Road Wandering Creek 6390 Western Australia<br><span>Phone</span>: (Aust) 08 97730158 | ph (International) 61 8 97730158<br><span>Fax</span>: (Aust) 08 97730162 | ph (International) 61 8 97730162</p>
<div class="foot-rule abs" style="left:382px"></div>
<h3 class="foot-title abs" style="left:423px;font-weight:400">STAY CONNECTED</h3>
<span class="social abs" style="left:421px;background:#1b9ad6"></span>
<span class="social abs" style="left:458px;background:#e8403a"></span>
<span class="social abs" style="left:496px;background:#3f7ee8"></span>
<span class="social abs" style="left:534px;background:#e3b317"></span>
<div class="foot-rule abs" style="left:606px"></div>
<p class="copyright abs"><em>Kestrel.Inc</em> © 2015 • Privacy Policy</p>
<p class="code abs">C16</p>
</body>
</html>
```